Yacht, Boats, Watersports company needs a redesign of business card

Hello Designers!
We are a Boat dealership company that sells fun in the water, we sell boats, Yachts, Kayaks and also yacht WaterSport toys. We are looking to redesign our business cards in to something a little bit more sophisticated. in a way that we can make better use of our company colors. I'm attaching a zipped file containing the company 3 sets of company logo which one is an horizontal another one is a vertical and also a chromed 3d logo. Also is included two set of business cards that we use and also some designs that i think it's interesting. We use PMS 2026c Orange and PMS 7687C Blue. I would like to see at least two different options with the orange as accent and also using blue as an accent color. It's really important for the business cards to have a font option and size that is legible to most people. Our current website is wwww.coralpennant.com. Please visit if you want to have a better feeling of the Boat dealership
You can send Single sided or double side options. We are now using single sided but we may be open for a double side option if we really like the design.
Target Market(s)
Marine, boat sales, yacht sales, water toys sales/
Contact Information for Business Card
Name: Dale Whitcombe
Address: 212 North Fenwick Lane,
Harbor Point, FL 33519
Phone: 954-731-8842
Fax: 954:731-8843
Cell: 954-382-1490
Email: dw@coralpennant.com
Website: coralpennant.com
Requirements
Must have
- the current information of the business card provided.
logo
use the PMS Colors
Nice to have
- a touch of elegance and sophistication but simple
Should not have
- should not have any typography that is hard to read, the card should be simple but yet sophisticated.

```html
<!DOCTYPE html>
<html lang="en">
<head>
<meta charset="utf-8">
<title>Coral Pennant — Business Card</title>
<link rel="stylesheet" href="https://fonts.googleapis.com/css2?family=Montserrat:wght@500;600;700&family=Oswald:wght@500&display=swap">
<style>
  :root {
    --page: #f3f3f3;
    --white: #ffffff;
    --navy-top: #10203a;
    --navy-bottom: #020d1a;
    --orange: #fd3f00;
    --brand-orange: #f26631;
    --brand-blue: #1a4579;
    --ink: #0b0b0b;
  }
  * { box-sizing: border-box; margin: 0; padding: 0; }
  html, body { width: 1200px; height: 1200px; overflow: hidden; }
  body { background: var(--page); position: relative; font-family: "Montserrat", sans-serif; }

  .card {
    position: absolute; left: 203px; width: 793px; height: 453px;
    border-radius: 38px; overflow: hidden; background: var(--white);
  }
  .card--front { top: 106px; }
  .card--back { top: 648px; }

  .card__shapes { position: absolute; inset: 0; }

  /* Front */
  .brand-mark {
    position: absolute; left: 0; right: 0; top: 66px;
    display: flex; flex-direction: column; align-items: center; gap: 20px;
  }
  .brand-mark__dot {
    width: 124px; height: 124px; border-radius: 50%;
    border: 11px solid var(--brand-orange);
  }
  .brand-mark__name {
    font-weight: 700; font-size: 42px; line-height: 1; letter-spacing: 6px;
    color: var(--brand-blue); text-transform: uppercase; white-space: nowrap;
  }
  .website {
    position: absolute; left: 162px; width: 474px; top: 283px; height: 75px;
    display: flex; align-items: center; justify-content: center;
    color: var(--white); font-weight: 600; font-size: 17px; letter-spacing: 2.4px;
    text-transform: uppercase;
  }

  /* Back */
  .person { position: absolute; left: 62px; top: 56px; }
  .person__name {
    font-family: "Oswald", sans-serif; font-weight: 500; font-size: 48px;
    line-height: 1; color: var(--ink); text-transform: uppercase; letter-spacing: 0;
  }
  .person__title {
    font-family: "Oswald", sans-serif; font-weight: 500; font-size: 21px;
    letter-spacing: 2.6px; color: var(--ink); margin-top: 4px; text-transform: uppercase;
  }
  .person__rule {
    width: 162px; height: 2px; background: var(--brand-blue); margin-top: 18px;
  }

  .back-mark {
    position: absolute; left: 52px; top: 270px; width: 180px;
    display: flex; flex-direction: column; align-items: center; gap: 14px;
  }
  .back-mark__dot {
    width: 96px; height: 96px; border-radius: 50%; border: 9px solid var(--white);
  }
  .back-mark__name {
    color: var(--white); font-weight: 700; font-size: 17px; letter-spacing: 1px;
    text-transform: uppercase; white-space: nowrap;
  }

  .contact {
    position: absolute; left: 424px; color: var(--white);
    font-weight: 500; font-size: 18px; line-height: 24px; letter-spacing: 0.6px;
  }
  .contact--address { top: 172px; }
  .contact--phones { top: 231px; }
  .contact--email { top: 317px; }
</style>
</head>
<body>

<section class="card card--front" aria-label="Business card front">
  <svg class="card__shapes" width="793" height="453" viewBox="0 0 793 453">
    <defs>
      <linearGradient id="navyFront" x1="0" y1="0" x2="0" y2="1">
        <stop offset="0" stop-color="#10203a"/>
        <stop offset="1" stop-color="#020d1a"/>
      </linearGradient>
    </defs>
    <rect x="0" y="321" width="793" height="132" fill="url(#navyFront)"/>
    <polygon points="182,283 616,283 636,320 616,358 182,358 162,320" fill="var(--orange)"/>
  </svg>
  <div class="brand-mark">
    <span class="brand-mark__dot" aria-hidden="true"></span>
    <span class="brand-mark__name">Coral Pennant</span>
  </div>
  <p class="website">wwww.coralpennant.com</p>
</section>

<section class="card card--back" aria-label="Business card back">
  <svg class="card__shapes" width="793" height="453" viewBox="0 0 793 453">
    <defs>
      <linearGradient id="navyBack" x1="0" y1="0" x2="0" y2="1">
        <stop offset="0" stop-color="#10203a"/>
        <stop offset="1" stop-color="#020d1a"/>
      </linearGradient>
    </defs>
    <rect x="0" y="237" width="793" height="216" fill="url(#navyBack)"/>
    <polygon points="351,122 793,122 793,391 368,391 284,237" fill="var(--orange)"/>

    <g class="contact-icons" fill="none" stroke="#fff" stroke-width="2">
      <line x1="390" y1="207" x2="390" y2="225"/>
      <line x1="390" y1="259" x2="390" y2="311"/>
      <circle cx="390" cy="190" r="17"/>
      <circle cx="390" cy="242" r="17"/>
      <circle cx="390" cy="328" r="17"/>
    </g>
    <path class="icon-pin" d="M390 199 C385 193 384 190 384 187.5 a6 6 0 0 1 12 0 C396 190 395 193 390 199 Z" fill="#fff"/>
    <circle cx="390" cy="187.5" r="2.2" fill="var(--orange)"/>
    <path class="icon-phone" d="M384.5 235.5 l3 -1 l2.2 4.6 l-2 1.6 c1 2.3 2.6 3.9 4.9 4.9 l1.6 -2 l4.6 2.2 l-1 3 c-7.5 0.5 -13.8 -5.8 -13.3 -13.3 Z" fill="#fff"/>
    <rect class="icon-mail" x="382" y="322" width="16" height="12" rx="1" fill="#fff"/>
    <path d="M382.5 323 L390 329 L397.5 323" fill="none" stroke="var(--orange)" stroke-width="1.5"/>
  </svg>

  <div class="person">
    <h1 class="person__name">Dale Whitcombe</h1>
    <p class="person__title">CEO &amp; Founder</p>
    <div class="person__rule"></div>
  </div>

  <div class="back-mark">
    <span class="back-mark__dot" aria-hidden="true"></span>
    <span class="back-mark__name">Coral Pennant</span>
  </div>

  <p class="contact contact--address">212 North Fenwick Lane,<br>Harbor Point, FL 33519</p>
  <p class="contact contact--phones">P: 954-731-8842<br>F: 954-731-8843<br>C: 954-382-1490</p>
  <p class="contact contact--email">dw@coralpennant.com</p>
</section>

</body>
</html>
```